Envelope Design Project

I will need two envelopes to be designed:-

DL size
C4 size

Please see uploaded documents for Design specs:

1) Design specs provided by printer (doc called DL Envelope Specs)
2) Design specs to comply with Kestrel Courier requirements (doc called Kestrel Courier Envelope Design Requirements)

Please adhere to the above for final design. Many thanks.

Target Market(s)

Real Estate Agents, Strata Managers, Builders, Architects, Business Owners

Industry/Entity Type

Printer

Requirements
Must have
• In top left corner
- Logo
- Return address - Suite 6, 19 Marlowe St, Wrenfield, NSW 2791

```html
<!DOCTYPE html>
<html lang="en">
<head>
<meta charset="utf-8">
<title>Quillbrook Hazard Care — Envelope Set</title>
<link rel="stylesheet" href="https://fonts.googleapis.com/css2?family=Questrial&display=swap">
<style>
  :root {
    --backdrop: #2b2b2b;
    --paper: #ffffff;
    --paper-edge: #d9d9d9;
    --brand-green: #9dc93b;
    --ink: #231f20;
    --ink-soft: #3a3a3a;
  }
  * { box-sizing: border-box; margin: 0; padding: 0; }
  html, body { width: 1200px; height: 900px; overflow: hidden; }
  body {
    position: relative;
    background: var(--backdrop);
    font-family: "Questrial", "Century Gothic", sans-serif;
    color: var(--ink);
  }
  .envelope {
    position: absolute;
    background: var(--paper);
    border: 1px solid var(--paper-edge);
    overflow: hidden;
  }

  /* C4 envelope */
  .c4-back { left: 168px; top: 86px; width: 630px; height: 445px; }
  .c4-back .flap-side { position: absolute; right: 0; top: 0; width: 76px; height: 100%; }
  .c4-front { left: 48px; top: 31px; width: 638px; height: 450px; overflow: visible; }

  /* DL envelope */
  .dl-back { left: 640px; top: 557px; width: 431px; height: 226px; }
  .dl-back .flap-top { position: absolute; left: 0; top: 0; width: 100%; height: 74px; }
  .dl-front { left: 559px; top: 647px; width: 433px; height: 215px; }

  /* Brand lockup */
  .brand {
    position: absolute;
    display: flex;
    align-items: center;
    gap: 7px;
    white-space: nowrap;
  }
  .brand-square { display: block; background: var(--brand-green); flex: none; }
  .brand-name { color: var(--ink); letter-spacing: 0.2px; }

  .c4-front .brand { left: 28px; top: 62px; }
  .c4-front .brand-square { width: 20px; height: 20px; }
  .c4-front .brand-name { font-size: 20px; }

  .dl-front .brand { left: 17px; top: 28px; }
  .dl-front .brand-square { width: 14px; height: 14px; }
  .dl-front .brand-name { font-size: 14px; }

  .dl-back .brand { left: 50%; top: 28px; transform: translateX(-50%); }
  .dl-back .brand-name { color: var(--paper); font-size: 12px; }

  /* Return address footer */
  .return-line {
    position: absolute;
    left: 0; right: 0;
    display: flex;
    align-items: center;
  }
  .return-line .lead-tick { width: 10px; height: 2px; background: var(--ink); flex: none; }
  .return-line .address { color: var(--ink-soft); white-space: nowrap; }
  .return-line .rule { flex: 1; height: 2px; background: var(--brand-green); }

  .c4-front .return-line { top: 420px; }
  .c4-front .address { font-size: 11px; margin: 0 17px 0 16px; }

  .dl-front .return-line { top: 201px; }
  .dl-front .lead-tick { width: 0; }
  .dl-front .address { font-size: 7.5px; margin: 0 10px 0 17px; }
</style>
</head>
<body>

  <section class="envelope c4-back" aria-label="C4 envelope, back">
    <svg class="flap-side" viewBox="0 0 76 445" preserveAspectRatio="none" aria-hidden="true">
      <path d="M76 0 H56 Q0 0 0 56 V389 Q0 445 56 445 H76 Z" fill="var(--brand-green)"/>
    </svg>
  </section>

  <section class="envelope c4-front" aria-label="C4 envelope, front">
    <div class="brand">
      <span class="brand-square"></span>
      <span class="brand-name">Quillbrook Hazard Care</span>
    </div>
    <div class="return-line">
      <span class="lead-tick"></span>
      <span class="address">Suite 6, 19 Marlowe St, Wrenfield, NSW 2791</span>
      <span class="rule"></span>
    </div>
  </section>

  <section class="envelope dl-back" aria-label="DL envelope, back">
    <svg class="flap-top" viewBox="0 0 431 74" preserveAspectRatio="none" aria-hidden="true">
      <path d="M0 0 H431 V10 Q431 74 367 74 H64 Q0 74 0 10 Z" fill="var(--brand-green)"/>
    </svg>
    <div class="brand">
      <span class="brand-name">Quillbrook Hazard Care</span>
    </div>
  </section>

  <section class="envelope dl-front" aria-label="DL envelope, front">
    <div class="brand">
      <span class="brand-square"></span>
      <span class="brand-name">Quillbrook Hazard Care</span>
    </div>
    <div class="return-line">
      <span class="lead-tick"></span>
      <span class="address">Suite 6, 19 Marlowe St, Wrenfield, NSW 2791</span>
      <span class="rule"></span>
    </div>
  </section>

</body>
</html>
```